2-Page Flyer for the Information Session about the Quiet Pathfinder Course

This is a flyer to announce/advertise an evening Information Session about the Quiet Pathfinder Course. This Program aims at mindfully rethinking and redesigning work (and life) for people who feel stuck or not entirely satisfied with their work and/or life (please see draft flyer attached for more details). This Program is property of Bright Meadow, a company that uses a combination of Mindfulness, Design, and Entrepreneurship to help people achieve greater happiness (in their work and lives).

Target Market(s)

People who feel stuck or not entirely satisfied with their work and/or life (please see draft flyer attached for more details)

Font styles to use
Serif
Sans Serif

Colors
ffffff
f37122
33a6d7
acd037

Requirements
Must have
• All of what I will say below is suggestive (I’m not a design expert), and I’m open to divert from it, if it makes sense and feels more interesting.
• I thought initially of a 2-page flyer (please see draft flyer attached). The first page could help people grasp the essence of the event quickly (in 1 or 2 minutes), and then, if they are interested/motivated, they would continue reading through page 2, which has more info about the Program in itself.
• Potential Structure
• Page 1
• . About the Information Session on the Quiet Pathfinder Course
• . Visible Date & Time, Contacts, Venue (and other relevant info)
• . About me (the facilitator)
• Page 2
• . About the Quiet Pathfinder Course
• I include a Powerpoint draft of the flyer with the content. The design is rudimentary and precarious from an aesthetics/organization point of view, and this is mainly where I need help (and maybe in other aspects too!).
• On the flyer, I would like to include:
• . A photo of myself (I attach 1 picture).
• . 1 or 2 beautiful-nature photos (cropped or full). One may have to do with looking at the sky, dreaming, and imagining a new work and life (2 photos with sky and clouds attached). The other has to do with walking the transformation journey (the photo with the person walking through the forest path).
• . bright meadow logo or logos (there are two slightly different ones, that can be used for different purposes). For the first page, I would like the bright meadow logo that has "bright meadow" written on the bottom, with the saying "Stillness, Craft and Venture for Bright Meadow" beneath. This is the main logo. For the 2nd page, you can choose the logo that adapts better.
• - Where it says the "the way out is in" it would be great to have a similar font to the one I attach (see file "Font_the_way_out_is_in.png" and Ankecallig-fg.ttf
Nice to have
• In terms of colours, I would not divert much from the logo colours (and of course white and black). I would like the flyer to be quite white. Almost like fairy-tale white: the white horse, the white snow, the white of the stars, the white heaven. White could be the base colour. White means peace, tranquillity, calm contentment, a smile.
• And then use the other colours. The green of the mindfulness. The blue of the sky, the dreams. And the orange of the sun, the energy, the fire, the action. And maybe the black for text.
• Where it says the "the way out is in" it would be great to have a similar font to the one I attach (see file "Font_the_way_out_is_in".
• I would like this flyer to be a piece of art, in every possible way. Simple, beautiful, ease, light, peaceful, calm happy. Just like the Quiet Pathfinder Course and bright meadow Company that I am creating intends to be. The mission of this Program and Company is to be a designer, a painter (a Picasso) of happier and more fulfilling human lives.
• I am very much looking forward to seeing your proposal(s).

```html
<!DOCTYPE html>
<html lang="en">
<head>
<meta charset="utf-8">
<title>Quiet Pathfinder Course – Information Session Flyer</title>
<link rel="stylesheet" href="https://fonts.googleapis.com/css2?family=Bebas+Neue&family=Montserrat:wght@300&family=Open+Sans:ital,wght@0,400;0,600;0,700;1,600;1,700&family=Satisfy&display=swap">
<style>
:root{
  --white:#ffffff;
  --orange:#f37122;
  --blue:#33a6d7;
  --green:#acd037;
  --ink:#222a30;
  --text:#3a3f44;
  --grey:#9aa0a6;
  --stage:#e9eaec;
  --sky-top:#8fbfe0;
  --sky-mid:#cfe3f1;
  --hills:#4d6f8c;
  --dusk:#2b3a45;
}
*{box-sizing:border-box;margin:0;padding:0}
html,body{width:1200px;height:808px;overflow:hidden}
body{background:var(--stage);font-family:"Open Sans",sans-serif;color:var(--text);position:relative}
.page{position:absolute;top:71px;width:494px;height:696px;background:var(--white);overflow:hidden;box-shadow:0 6px 22px rgba(0,0,0,.18)}
.page--front{left:81px}
.page--back{left:626px}
.abs{position:absolute}

/* FRONT */
.side-band{left:0;top:0;width:96px;height:696px;background:var(--green);border-radius:0 48px 48px 0}
.side-band__title{position:absolute;left:0;top:0;width:96px;height:696px;display:flex;align-items:center;justify-content:center}
.side-band__title span{writing-mode:vertical-rl;transform:rotate(180deg);font-family:"Montserrat",sans-serif;font-weight:300;font-size:44px;letter-spacing:4px;color:var(--white);white-space:nowrap}
.hero{left:96px;top:0;width:398px;height:322px;background:linear-gradient(180deg,var(--sky-mid) 0%,var(--white) 22%,var(--sky-mid) 45%,var(--sky-top) 62%,var(--hills) 80%,var(--dusk) 100%)}
.hero__shade{left:96px;top:260px;width:398px;height:62px;background:rgba(30,40,48,.55)}
.brand{left:147px;top:30px;display:flex;align-items:center;gap:12px}
.brand__dot{width:60px;height:60px;border-radius:50%;background:var(--blue)}
.brand__name{font-family:"Open Sans",sans-serif;font-weight:400;font-size:36px;line-height:32px;color:var(--orange)}
.brand-tagline{left:150px;top:100px;width:280px;text-align:right;font-size:8.5px;color:var(--ink)}
.title{left:96px;top:127px;width:398px;text-align:center;font-family:"Bebas Neue",sans-serif;font-weight:400;font-size:50px;line-height:39px}
.title__a{display:block;color:var(--green)}
.title__b{display:block;color:var(--ink)}
.title__c{display:block;color:var(--white)}
.when{left:96px;top:265px;width:398px;text-align:center;color:var(--white);font-size:20px;line-height:24px}
.when__date{letter-spacing:-.3px}
.when__date b{font-weight:700}
.intro{left:113px;top:336px;width:359px;font-size:8px;line-height:10px;text-align:justify}
.heading-green{left:113px;top:376px;width:359px;display:flex;align-items:center;gap:4px;font-weight:700;font-size:14px;line-height:18px;color:var(--green)}
.heading-green::after{content:"";flex:1;height:1.5px;background:var(--green);margin-top:6px}
.who{left:113px;top:397px;width:359px;font-size:8px;line-height:10px;text-align:justify}
.facilitator{left:112px;top:445px;width:120px;height:156px;border:1px solid #e3e5e8;background:var(--white)}
.facilitator__label{position:absolute;left:0;top:5px;width:100%;text-align:center;font-size:11px;letter-spacing:3.5px;color:var(--grey)}
.facilitator__photo{position:absolute;left:6px;top:23px;width:107px;height:127px;background:linear-gradient(160deg,#dfe3e6,#a9b0b6 60%,#3d4a58)}
.bio-name{left:250px;top:436px;font-size:17px;line-height:22px;font-weight:600;color:var(--ink)}
.bio-role{left:250px;top:463px;font-size:7.5px;line-height:10px;font-style:italic;color:var(--orange)}
.bio{left:250px;top:481px;width:222px;font-size:6.8px;line-height:8.95px;text-align:justify}
.booking-tab{height:29px;display:flex;align-items:center;font-weight:700;font-style:italic;font-size:16px;color:var(--white)}
.booking-tab--front{left:96px;top:614px;width:217px;background:var(--blue);border-radius:0 22px 0 0;padding-left:20px}
.phone{display:flex;align-items:center;gap:6px;font-family:"Bebas Neue",sans-serif;font-weight:400;font-size:31px;line-height:34px;color:var(--ink);white-space:nowrap}
.phone--front{left:114px;top:651px}
.contacts{font-size:10px;line-height:14.5px;color:var(--ink);white-space:nowrap}
.contacts__row{display:flex;align-items:center;gap:8px}
.contacts__row--addr{align-items:flex-start}
.contacts--front{left:310px;top:644px}

/* BACK */
.back-sky{left:0;top:0;width:494px;height:330px;background:linear-gradient(180deg,var(--sky-mid) 0%,#eef5fa 35%,#dfeaf2 60%,var(--white) 100%)}
.back-h1{left:25px;top:16px;font-size:15.5px;font-weight:700;color:var(--orange)}
.back-lead{left:25px;top:40px;width:443px;font-size:8.7px;line-height:11px;text-align:justify;color:var(--ink)}
.tab{height:20px;display:flex;align-items:center;font-weight:700;font-size:14px;color:var(--white);padding-left:25px;border-radius:0 12px 12px 0}
.tab--program{left:0;top:99px;width:137px;background:var(--orange)}
.tab--why{left:0;top:285px;width:80px;background:var(--blue)}
.tab--how{left:245px;top:285px;width:68px;background:var(--green);padding-left:13px}
.program-text{left:25px;top:132px;width:206px;font-size:8.6px;line-height:10.9px;text-align:justify;color:var(--ink)}
.program-text p+p{margin-top:11px}
.cycle{left:0;top:0}
.how-rule{left:245px;top:285px;width:1.5px;height:205px;background:var(--green)}
.col{font-size:8.8px;line-height:10.9px;color:var(--ink)}
.col--why{left:25px;top:318px;width:208px;text-align:justify}
.col--how{left:259px;top:318px;width:210px}
.checks{list-style:none;margin-top:7px}
.checks li{display:flex;gap:6px;margin-bottom:6px;text-align:left}
.checks svg{flex:none;margin-top:2px}
.forest{left:0;top:491px;width:494px;height:123px;background:linear-gradient(180deg,#2f3a22 0%,#5a5232 45%,#3b3b25 100%);border-radius:0 0 0 40px}
.forest__motto{left:0;top:518px;width:494px;text-align:center;font-family:"Satisfy",cursive;font-size:38px;line-height:46px;color:var(--white)}
.brand--back{left:22px;top:624px;flex-direction:column;gap:2px}
.brand--back .brand__dot{width:30px;height:30px}
.brand--back .brand__name{font-size:15px;line-height:16px;color:var(--blue)}
.booking-tab--back{left:133px;top:614px;width:361px;background:var(--orange);border-radius:22px 0 0 0;justify-content:center;padding-left:30px}
.phone--back{left:148px;top:652px}
.contacts--back{left:342px;top:649px;font-size:8.8px;line-height:12.5px}
</style>
</head>
<body>

<section class="page page--front" aria-label="Flyer front">
  <div class="abs hero" role="img" aria-label="Photo of sky, clouds and blue mountain ranges"></div>
  <div class="abs hero__shade"></div>

  <div class="abs brand">
    <span class="brand__dot"></span>
    <span class="brand__name">bright<br>meadow</span>
  </div>
  <p class="abs brand-tagline">Stillness, Craft and Venture for Bright Meadow</p>

  <h1 class="abs title">
    <span class="title__a">QUIET</span>
    <span class="title__b">PATHFINDER</span>
    <span class="title__c">COURSE</span>
  </h1>

  <div class="abs when">
    <p class="when__date">Thursday <b>5th September 2019</b></p>
    <p class="when__time">19:30 to 21:00</p>
  </div>

  <div class="abs side-band">
    <div class="side-band__title"><span>INFORMATION SESSION</span></div>
  </div>

  <p class="abs intro">The purpose of this Information Session is to give you a real insight into the Quiet Pathfinder Course and how it can help you make the most of your professional and personal life.</p>

  <h2 class="abs heading-green">WHO CAN COME</h2>
  <p class="abs who">The Information Session is free. Whether you come on your own, or with friends or family, you’ll be warmly welcome. It will take place on Thursday the 5th September 2019, from 19:30 to 21:00, at Lumen Coworking. Please get in touch for more info or to book a place.</p>

  <div class="abs facilitator">
    <span class="facilitator__label">FACILITATOR</span>
    <div class="facilitator__photo" role="img" aria-label="Portrait photo of the facilitator"></div>
  </div>
  <h3 class="abs bio-name">Dr Tomas Reyes</h3>
  <p class="abs bio-role">Visiting Research Fellow, Harwick University</p>
  <p class="abs bio">Tomas joined Harwick University (School of Management) as a Lecturer in Entrepreneurship in 2015. He completed his PhD in Entrepreneurship at Northvale Business School in 2014. His work received the Lindqvist Doctoral Dissertation Award from the Society of Management Studies. He began his business career as a production engineer (Corvant), and continued in sales (Heltrix). After his MBA, he worked as a strategy consultant at Lisbra Business School. Originally from Portugal, Tomas enjoys designing and launching new ideas, international communities, mindfulness retreats, and musical improvisation. He nurtures a close connection to Willow Hollow Mindfulness Centre, where he has practiced and volunteered over 9 months. He has a broad experience of sharing the benefits of mindfulness with others.</p>

  <div class="abs booking-tab booking-tab--front">Information &amp; Booking</div>
  <div class="abs phone phone--front">
    <svg width="10" height="22" viewBox="0 0 10 22" aria-hidden="true"><path d="M8 2 Q2 3 2 11 Q2 19 8 20" fill="none" stroke="var(--blue)" stroke-width="3" stroke-linecap="round"/></svg>
    +34 611 482 305
  </div>
  <div class="abs contacts contacts--front">
    <div class="contacts__row">
      <svg width="10" height="8" viewBox="0 0 10 8" aria-hidden="true"><rect width="10" height="8" rx="1" fill="var(--blue)"/><path d="M0.5 1 5 4.5 9.5 1" fill="none" stroke="#fff" stroke-width="1"/></svg>
      info@brightmeadow.io
    </div>
    <div class="contacts__row contacts__row--addr">
      <svg width="10" height="12" viewBox="0 0 10 12" aria-hidden="true" style="margin-top:2px"><path d="M5 12 C1 7 1 5 1 4.5 A4 4 0 0 1 9 4.5 C9 5 9 7 5 12Z" fill="var(--blue)"/><circle cx="5" cy="4.5" r="1.5" fill="#fff"/></svg>
      <span>Lumen Coworking, C/ Roble 42,<br>Barcelona</span>
    </div>
  </div>
</section>

<section class="page page--back" aria-label="Flyer back">
  <div class="abs back-sky" role="img" aria-label="Soft photo of sky and clouds fading to white"></div>

  <h2 class="abs back-h1">What is Mindful Entrepreneurship</h2>
  <p class="abs back-lead">Being mindful means being aware and awake. Entrepreneurship is the creation of a new form of organising. Mindful Entrepreneurship is then the process of creating or redesigning your work and life with awareness, in a way that is reflective of you, of your passions and values, thus conducing to a greater sense of fulfilment and happiness.</p>

  <div class="abs tab tab--program">THE PROGRAM</div>
  <div class="abs program-text">
    <p><b>The Quiet Pathfinder Course</b> is a <b>4-month long transformative journey</b> designed for people who feel stuck or not entirely satisfied with their professional and/or personal life. It will be of benefit for everyone, at any stage.</p>
    <p>The Program consists of a 5-hour workshop every month, complemented by 2-hour weekly peer support meetings. It combines mindfulness techniques, design thinking methodology, and entrepreneurship frameworks.</p>
  </div>

  <svg class="abs cycle" width="494" height="290" viewBox="0 0 494 290" aria-label="Cycle of four workshops joined by weekly peer support meetings" role="img">
    <defs>
      <marker id="head" viewBox="0 0 10 10" refX="5" refY="5" markerWidth="4" markerHeight="4" orient="auto"><path d="M0 0 10 5 0 10Z" fill="context-stroke"/></marker>
    </defs>
    <g font-family="Open Sans, sans-serif" text-anchor="middle" fill="#fff">
      <circle cx="352" cy="119" r="33" fill="var(--green)"/>
      <text x="352" y="112" font-size="7.5">Workshop 1</text>
      <text x="352" y="122" font-size="8.5" font-weight="700">INSIGHT</text>
      <text x="352" y="131" font-size="7" font-style="italic">(5 hours)</text>

      <circle cx="424" cy="176" r="33" fill="var(--blue)"/>
      <text x="424" y="169" font-size="7.5">Workshop 2</text>
      <text x="424" y="179" font-size="8.5" font-weight="700">DESIGN</text>
      <text x="424" y="188" font-size="7" font-style="italic">(5 hours)</text>

      <circle cx="352" cy="233" r="33" fill="var(--orange)"/>
      <text x="352" y="226" font-size="7.5">Workshop 3</text>
      <text x="352" y="236" font-size="8.5" font-weight="700">EXECUTE</text>
      <text x="352" y="245" font-size="7" font-style="italic">(5 hours)</text>

      <circle cx="287" cy="176" r="33" fill="#b9bdc1"/>
      <text x="287" y="169" font-size="7.5">Workshop 4</text>
      <text x="287" y="179" font-size="8.5" font-weight="700">PRESENT</text>
      <text x="287" y="188" font-size="7" font-style="italic">(5 hours)</text>
    </g>
    <g fill="none" stroke-width="2.5" marker-end="url(#head)">
      <line x1="392" y1="134" x2="405" y2="147" stroke="var(--green)"/>
      <line x1="410" y1="210" x2="398" y2="221" stroke="var(--blue)"/>
      <line x1="314" y1="219" x2="303" y2="210" stroke="var(--orange)"/>
      <line x1="312" y1="143" x2="323" y2="132" stroke="#c3c6c9"/>
    </g>
    <g font-family="Open Sans, sans-serif" font-size="7" font-style="italic" fill="#555b60" text-anchor="middle">
      <text x="283" y="131">WPS meetings</text>
      <text x="283" y="234">WPS meetings</text>
      <text x="420" y="234">WPS meetings</text>
      <text x="426" y="116">Weekly Peer Support</text>
      <text x="426" y="125">(WPS) meetings</text>
      <text x="426" y="134">(2 hours)</text>
    </g>
  </svg>

  <div class="abs tab tab--why">WHY</div>
  <div class="abs how-rule"></div>
  <div class="abs tab tab--how">HOW</div>

  <div class="abs col col--why">
    <p>Many people are not satisfied with their work or life, but they don’t know what to do about it. This Program offers you a safe place to conduct your inner journey with collective support, helping you reflect, design, and (very likely) do something about it. It aims at:</p>
    <ul class="checks">
      <li><svg width="8" height="8" viewBox="0 0 8 8" aria-hidden="true"><rect x=".5" y=".5" width="7" height="7" rx="1" fill="none" stroke="var(--green)"/><path d="M2 4 3.5 5.5 7 1.5" fill="none" stroke="var(--green)" stroke-width="1.3"/></svg>Increasing awareness, clarity and confidence</li>
      <li><svg width="8" height="8" viewBox="0 0 8 8" aria-hidden="true"><rect x=".5" y=".5" width="7" height="7" rx="1" fill="none" stroke="var(--green)"/><path d="M2 4 3.5 5.5 7 1.5" fill="none" stroke="var(--green)" stroke-width="1.3"/></svg>Having a deeper insight on what makes you happier and what you want</li>
      <li><svg width="8" height="8" viewBox="0 0 8 8" aria-hidden="true"><rect x=".5" y=".5" width="7" height="7" rx="1" fill="none" stroke="var(--green)"/><path d="M2 4 3.5 5.5 7 1.5" fill="none" stroke="var(--green)" stroke-width="1.3"/></svg>Developing a clear design integrating your intended work and life</li>
      <li><svg width="8" height="8" viewBox="0 0 8 8" aria-hidden="true"><rect x=".5" y=".5" width="7" height="7" rx="1" fill="none" stroke="var(--green)"/><path d="M2 4 3.5 5.5 7 1.5" fill="none" stroke="var(--green)" stroke-width="1.3"/></svg>Start executing this design.</li>
    </ul>
  </div>

  <div class="abs col col--how">
    <p>This Program differs from existing entrepreneurial programs in many ways:</p>
    <ul class="checks">
      <li><svg width="8" height="8" viewBox="0 0 8 8" aria-hidden="true"><rect x=".5" y=".5" width="7" height="7" rx="1" fill="none" stroke="var(--blue)"/><path d="M2 4 3.5 5.5 7 1.5" fill="none" stroke="var(--blue)" stroke-width="1.3"/></svg>Uses mindfulness and self analysis to look deeply into yourself</li>
      <li><svg width="8" height="8" viewBox="0 0 8 8" aria-hidden="true"><rect x=".5" y=".5" width="7" height="7" rx="1" fill="none" stroke="var(--blue)"/><path d="M2 4 3.5 5.5 7 1.5" fill="none" stroke="var(--blue)" stroke-width="1.3"/></svg>Design and execution decisions are based on happiness rather than (only) financials</li>
      <li><svg width="8" height="8" viewBox="0 0 8 8" aria-hidden="true"><rect x=".5" y=".5" width="7" height="7" rx="1" fill="none" stroke="var(--blue)"/><path d="M2 4 3.5 5.5 7 1.5" fill="none" stroke="var(--blue)" stroke-width="1.3"/></svg>Holistic and inclusive design process, integrating work and life, and building synergies between your different parts.</li>
    </ul>
    <p>The Program format includes lectures, individual work, group sharing, guided activities, experiential exercises, video, audio, handouts and other resources.</p>
  </div>

  <div class="abs forest" role="img" aria-label="Photo of a person walking along a forest path between tall trees"></div>
  <p class="abs forest__motto">The way out is in</p>

  <div class="abs brand brand--back">
    <span class="brand__dot"></span>
    <span class="brand__name">bright meadow</span>
  </div>

  <div class="abs booking-tab booking-tab--back">Information &amp; Booking</div>
  <div class="abs phone phone--back">
    <svg width="10" height="22" viewBox="0 0 10 22" aria-hidden="true"><path d="M8 2 Q2 3 2 11 Q2 19 8 20" fill="none" stroke="var(--orange)" stroke-width="3" stroke-linecap="round"/></svg>
    +34 611 482 305
  </div>
  <div class="abs contacts contacts--back">
    <div class="contacts__row">
      <svg width="10" height="8" viewBox="0 0 10 8" aria-hidden="true"><rect width="10" height="8" rx="1" fill="var(--orange)"/><path d="M0.5 1 5 4.5 9.5 1" fill="none" stroke="#fff" stroke-width="1"/></svg>
      info@brightmeadow.io
    </div>
    <div class="contacts__row contacts__row--addr">
      <svg width="10" height="12" viewBox="0 0 10 12" aria-hidden="true" style="margin-top:1px"><path d="M5 12 C1 7 1 5 1 4.5 A4 4 0 0 1 9 4.5 C9 5 9 7 5 12Z" fill="var(--orange)"/><circle cx="5" cy="4.5" r="1.5" fill="#fff"/></svg>
      <span>Lumen Coworking, C/ Roble 42,<br>Barcelona</span>
    </div>
  </div>
</section>

</body>
</html>
```